Animal Eye Clinic needs a Business card

We are a new veterinary ophthalmology practice (Ridgeline Pet Vision Care) and we need a business card designed. We only see animal eyes - we are not a regular veterinary clinic. We already have a logo. We are looking for a professional, good looking business card to hand out to our clients. We are looking for something simple but professional and contemporary. Our logo is likely the only picture/graphic that needs to be on the card.
Updates

Contact Information for Business Card

Delia Vossman, BSc, DVM, MSc, DipACVO
Veterinary Ophthalmologist

Phone: 250.418.3927
Email: ridgelinepetvisioncare@mailbox-example.net
Website: ridgelinepetvisioncare-example.net
Address: 1874 Thornbury Rd
Kelowna, BC, V1X 4M9

Colors

Designer to choose colors to be used in the design.

Requirements
Must have
• Our logo (attached)

```html
<!DOCTYPE html>
<html lang="en">
<head>
<meta charset="utf-8">
<title>Ridgeline Pet Vision Care – Business Card</title>
<link rel="stylesheet" href="https://fonts.googleapis.com/css2?family=Lato:wght@300;400;700&family=Libre+Baskerville:wght@700&display=swap">
<style>
  :root {
    --page-bg: #eef0f1;
    --card-bg: #ffffff;
    --ink-grey: #7d7f81;
    --ink-soft: #8e9092;
    --teal: #3aa3b0;
  }
  * { box-sizing: border-box; margin: 0; padding: 0; }
  html, body {
    width: 1200px;
    height: 900px;
    overflow: hidden;
    background: var(--page-bg);
  }
  .stage {
    width: 1200px;
    height: 900px;
    display: flex;
    align-items: center;
    justify-content: center;
  }
  .business-card {
    position: relative;
    width: 1000px;
    height: 571px;
    background: var(--card-bg);
    box-shadow: 0 2px 10px rgba(0,0,0,0.08);
    font-family: "Lato", sans-serif;
    color: var(--ink-grey);
  }
  .identity {
    position: absolute;
    left: 90px;
    top: 96px;
  }
  .identity__name-row {
    display: flex;
    align-items: baseline;
    gap: 22px;
  }
  .identity__name {
    font-family: "Libre Baskerville", serif;
    font-weight: 700;
    font-size: 58px;
    color: var(--ink-grey);
  }
  .identity__credentials {
    font-weight: 400;
    font-size: 17px;
    letter-spacing: 4px;
    color: var(--ink-soft);
    position: relative;
    top: -26px;
  }
  .identity__title {
    margin-top: 4px;
    font-weight: 400;
    font-size: 32px;
    letter-spacing: 7px;
    color: var(--ink-soft);
  }
  .identity__dots {
    display: flex;
    gap: 30px;
    margin-top: 26px;
    margin-left: 6px;
  }
  .identity__dots span {
    width: 7px;
    height: 7px;
    border-radius: 50%;
    background: var(--teal);
  }
  .brand {
    position: absolute;
    right: 70px;
    top: 318px;
    display: flex;
    align-items: center;
    gap: 14px;
  }
  .brand__dot {
    width: 26px;
    height: 26px;
    border-radius: 50%;
    background: var(--teal);
  }
  .brand__name {
    font-weight: 700;
    font-size: 26px;
    color: var(--teal);
  }
  .contact {
    position: absolute;
    left: 150px;
    top: 392px;
    display: grid;
    grid-template-columns: 90px auto;
    row-gap: 6px;
    font-size: 22px;
    line-height: 28px;
  }
  .contact__label {
    color: var(--teal);
    font-weight: 400;
    letter-spacing: 1px;
  }
  .contact__value {
    color: var(--ink-grey);
    font-weight: 300;
  }
</style>
</head>
<body>
  <main class="stage">
    <section class="business-card">
      <div class="identity">
        <div class="identity__name-row">
          <h1 class="identity__name">Delia Vossman</h1>
          <span class="identity__credentials">BSc, DVM, MSc, DipACVO</span>
        </div>
        <p class="identity__title">Veterinary Ophthalmologist</p>
        <div class="identity__dots"><span></span><span></span><span></span></div>
      </div>

      <div class="brand">
        <span class="brand__dot"></span>
        <span class="brand__name">Ridgeline Pet Vision Care</span>
      </div>

      <dl class="contact">
        <dt class="contact__label">P:</dt>
        <dd class="contact__value">250.418.3927</dd>
        <dt class="contact__label">E:</dt>
        <dd class="contact__value">ridgelinepetvisioncare@mailbox-example.net</dd>
        <dt class="contact__label">W:</dt>
        <dd class="contact__value">ridgelinepetvisioncare-example.net</dd>
        <dt class="contact__label">Add:</dt>
        <dd class="contact__value">1874 Thornbury Rd Kelowna, BC, V1X 4M9</dd>
      </dl>
    </section>
  </main>
</body>
</html>
```